Dalvick's Business Card

I need some designs for a new business card including the new logo attached. An old example of our business card is also attached to show all the data that should be included on the new design.
**I added some more examples someone had mocked up**

Contact Information for Business Card

Should include all info on other examples uploaded.

```html
<!DOCTYPE html>
<html lang="en">
<head>
<meta charset="utf-8">
<title>Dalvick's Business Card</title>
<link rel="stylesheet" href="https://fonts.googleapis.com/css2?family=Montserrat:wght@500;600;700;800&display=swap">
<style>
  :root {
    --brand-blue: #0b72b9;
    --brand-red: #e82128;
    --paper: #ffffff;
    --backdrop: #e6e5e6;
  }
  * { box-sizing: border-box; margin: 0; padding: 0; }
  html, body { width: 1200px; height: 1200px; overflow: hidden; background: var(--backdrop); }
  body {
    font-family: "Montserrat", sans-serif;
    display: flex; flex-direction: column; align-items: center; justify-content: center;
    gap: 56px;
  }
  .card {
    position: relative; width: 900px; height: 514px; overflow: hidden;
    background: var(--paper);
    box-shadow: 0 10px 30px rgba(0,0,0,0.18);
  }
  .card-art { position: absolute; inset: 0; width: 100%; height: 100%; }

  /* Front */
  .band-text {
    position: absolute; left: 0; right: 0; color: var(--paper);
    font-weight: 500; text-transform: uppercase; text-align: center; letter-spacing: 0.02em;
  }
  .band-text.top { top: 26px; font-size: 28px; }
  .band-text.bottom { bottom: 24px; font-size: 21px; }
  .front-logo {
    position: absolute; top: 50%; left: 50%; transform: translate(-50%, -50%);
    display: flex; align-items: center; gap: 22px;
  }
  .logo-dot { width: 74px; height: 74px; border-radius: 50%; background: var(--brand-red); flex: none; }
  .logo-name { font-weight: 700; font-size: 86px; line-height: 1; color: var(--paper); letter-spacing: 0.01em; }

  /* Back */
  .owner-name {
    position: absolute; left: 64px; top: 150px;
    color: var(--brand-red); font-weight: 800; font-size: 38px; letter-spacing: 0.02em; text-transform: uppercase;
  }
  .back-logo { position: absolute; left: 440px; top: 78px; display: flex; align-items: center; gap: 14px; }
  .back-logo .logo-dot { width: 52px; height: 52px; }
  .back-logo .logo-name { color: var(--brand-blue); font-size: 58px; }
  .contact {
    position: absolute; left: 78px; top: 332px; color: var(--paper);
    list-style: none; font-size: 22px; font-weight: 500; line-height: 1.35;
  }
  .contact li { display: flex; align-items: center; gap: 10px; }
  .contact svg { width: 20px; height: 20px; flex: none; }
  .contact .credential { text-transform: uppercase; font-size: 23px; }
  .contact .credential.first { margin-top: 14px; }
</style>
</head>
<body>

  <section class="card card-front" aria-label="Card front">
    <svg class="card-art" viewBox="0 0 900 514" aria-hidden="true">
      <rect width="900" height="514" fill="var(--brand-blue)"/>
      <polygon points="0,0 900,0 900,88 400,88 380,116 360,88 0,88" fill="var(--brand-red)"/>
      <polygon points="0,430 500,430 520,402 540,430 900,430 900,514 0,514" fill="var(--brand-red)"/>
    </svg>
    <p class="band-text top">Serves Maple Falls, IA &amp; Surrounding Areas</p>
    <div class="front-logo">
      <span class="logo-dot"></span>
      <span class="logo-name">DALVICK'S</span>
    </div>
    <p class="band-text bottom">Call today for all your HVAC, refrigeration &amp; plumbing needs</p>
  </section>

  <section class="card card-back" aria-label="Card back">
    <svg class="card-art" viewBox="0 0 900 514" aria-hidden="true">
      <rect width="900" height="514" fill="var(--paper)"/>
      <path d="M520,262 C740,262 870,210 900,40 L900,514 L520,514 Z" fill="var(--brand-red)"/>
      <path d="M0,330 C110,240 300,232 480,250 C620,264 760,270 840,225 C868,208 888,180 900,150 L900,514 L0,514 Z" fill="var(--brand-blue)"/>
    </svg>
    <div class="back-logo">
      <span class="logo-dot"></span>
      <span class="logo-name">DALVICK'S</span>
    </div>
    <h1 class="owner-name">Mark Dalvick</h1>
    <ul class="contact">
      <li>
        <svg viewBox="0 0 24 24" aria-hidden="true"><path fill="#fff" d="M6.6 10.8a15.1 15.1 0 0 0 6.6 6.6l2.2-2.2c.3-.3.7-.4 1-.2 1.1.4 2.3.6 3.6.6.6 0 1 .4 1 1V20c0 .6-.4 1-1 1A17 17 0 0 1 3 4c0-.6.4-1 1-1h3.5c.6 0 1 .4 1 1 0 1.3.2 2.5.6 3.6.1.3 0 .7-.2 1z"/></svg>
        555.014.2290
      </li>
      <li>
        <svg viewBox="0 0 24 24" aria-hidden="true"><path fill="#fff" d="M2 5h20v14H2z"/><path fill="none" stroke="#0b72b9" stroke-width="1.8" d="M2 5l10 8 10-8"/></svg>
        hvacdalvick@mailbox.com
      </li>
      <li class="credential first">Licensed &amp; Insured</li>
      <li class="credential">Family Owned &amp; Operated</li>
    </ul>
  </section>

</body>
</html>
```